Creative, fresh business card design for Ripplecraft Facades

We need a fresh, creative business card design for Ripplecraft Facades. We are the manufacturer of Ripplecraft Facades in Australia. Wall panels are 2400 x 1200mm panels made from MDF and feature 3D patterns on the face of the panel. The colours to be used are green, silver/grey and white RGB
Red 187
Green 207
Blue 65.

An idea is to possibly use a watermark of one of our designs as a background (like on the "Grids" design on the left hand side of page 2 of our brochure).

Target Market(s)

Interior designers, architects, builders and home renovators

Industry/Entity Type

Business

Contact Information for Business Card

Details to go on the card are:
Our logo (attached),
Slogan: "Decorative panels for interiors and exteriors",
Contact name,
Position,
Mobile phone number,
Business address,
Business phone,
Business fax,
Website and
Email address.

I have attached a few images of our panels and our brochure for reference.

The colours of the business card should feature our logo colours which are: RGB
Red 187
Green 207
Blue 65

Requirements
Must have
• Very modern fonts and design. Some of the designs shown especially the "Prisms" design which is a popular design.
Nice to have
• Creative but simple design. Very contemporary.
Should not have
• Anything ornate or old fashioned.

```html
<!DOCTYPE html>
<html lang="en">
<head>
<meta charset="utf-8">
<title>Ripplecraft Facades – Business Card</title>
<link rel="stylesheet" href="https://fonts.googleapis.com/css2?family=Arimo:ital,wght@0,400;0,700;1,400&display=swap">
<style>
  :root {
    --brand-green: #bbcf41;
    --steel-grey: #8b8d90;
    --rule-grey: #9a9a9a;
    --ink: #3a3a3a;
    --ink-dark: #2b2b2b;
    --paper: #ffffff;
    --backdrop: #e8e6e2;
  }
  * { box-sizing: border-box; margin: 0; padding: 0; }
  html, body { width: 1200px; height: 987px; overflow: hidden; }
  body {
    background: var(--backdrop);
    font-family: "Arimo", Arial, sans-serif;
    position: relative;
  }
  .card {
    position: absolute;
    width: 615px;
    height: 351px;
    left: 293px;
    box-shadow: 0 2px 8px rgba(0,0,0,0.18);
    overflow: hidden;
  }
  .card--front { top: 130px; background: var(--paper); }
  .card--back { top: 506px; background: var(--brand-green); }

  .brand {
    position: absolute;
    display: flex;
    align-items: center;
    gap: 10px;
    font-weight: 700;
    white-space: nowrap;
  }
  .brand__square { width: 22px; height: 22px; flex: none; }
  .card--front .brand {
    right: 35px; top: 88px;
    font-size: 26px; color: var(--brand-green);
  }
  .card--front .brand__square { background: var(--brand-green); }
  .tagline {
    position: absolute;
    font-size: 12.5px;
    letter-spacing: 2.6px;
    line-height: 15px;
    text-align: center;
    white-space: nowrap;
  }
  .card--front .tagline { right: 33px; top: 150px; color: var(--steel-grey); }

  .person__name {
    position: absolute; left: 30px; top: 175px;
    font-size: 22px; font-weight: 700; color: var(--brand-green);
    letter-spacing: 0.5px;
  }
  .person__role {
    position: absolute; left: 30px; top: 204px;
    font-size: 16.5px; color: var(--steel-grey);
  }
  .divider {
    position: absolute; left: 30px; top: 227px;
    width: 552px; height: 1px; background: var(--rule-grey);
  }
  .contact-list {
    position: absolute; left: 34px; top: 242px;
    list-style: none;
  }
  .contact-list li {
    display: flex; align-items: center; gap: 8px;
    height: 23px; font-size: 16px; color: var(--ink);
  }
  .contact-list svg { width: 14px; height: 14px; flex: none; }
  .address {
    position: absolute; right: 33px; top: 266px;
    font-size: 16px; line-height: 22px; color: var(--ink); text-align: right;
    font-style: normal;
  }
  .footer-band { position: absolute; left: 0; top: 0; }
  .website {
    position: absolute; right: 27px; top: 324px;
    font-size: 15.5px; font-style: italic; letter-spacing: 1.5px;
    color: var(--paper); white-space: nowrap;
  }

  .card--back .brand {
    left: 50%; top: 136px; transform: translateX(-50%);
    font-size: 30px; color: var(--ink-dark);
  }
  .card--back .brand__square { background: var(--ink-dark); width: 26px; height: 26px; }
  .card--back .tagline {
    left: 0; right: 0; top: 226px; color: var(--ink-dark);
    font-size: 13px; letter-spacing: 3px;
  }
</style>
</head>
<body>

<section class="card card--front" aria-label="Business card front">
  <div class="brand"><span class="brand__square"></span>Ripplecraft Facades</div>
  <p class="tagline">decorative panels for<br>interiors &amp; landscapes</p>

  <h1 class="person__name">MARCUS HALE</h1>
  <p class="person__role">CEO&amp;Founder</p>
  <div class="divider"></div>

  <ul class="contact-list">
    <li>
      <svg viewBox="0 0 16 16" aria-hidden="true"><path fill="#bbcf41" d="M3.6 1.2l2.3 2.9-1.3 1.6c.9 2 2.6 3.7 4.6 4.6l1.6-1.3 2.9 2.3-1.2 2.3C7.6 13.5 2.5 8.4 1.4 2.4z"/></svg>
      (555) 214-7730
    </li>
    <li>
      <svg viewBox="0 0 16 16" aria-hidden="true"><rect x="4" y="1.5" width="8" height="4" fill="#bbcf41"/><rect x="1" y="6" width="14" height="6" rx="1" fill="#bbcf41"/><rect x="4" y="10" width="8" height="4.5" fill="#fff" stroke="#bbcf41"/></svg>
      (555) 214-7731
    </li>
    <li>
      <svg viewBox="0 0 16 16" aria-hidden="true"><rect x="1" y="3" width="14" height="10" fill="#bbcf41"/><path d="M1.5 3.5L8 9l6.5-5.5" fill="none" stroke="#fff" stroke-width="1.2"/></svg>
      mhale@ripplecraftfacades.com
    </li>
  </ul>

  <address class="address">42 Fernleigh Road<br>Brookvale, NSW 2100</address>

  <svg class="footer-band" width="615" height="351" viewBox="0 0 615 351" aria-hidden="true">
    <polygon points="0,333 302,333 297,339 0,339" fill="#9a9a9a"/>
    <polygon points="312,317 615,317 615,351 0,351 0,345 300,345" fill="#bbcf41"/>
  </svg>
  <p class="website">www.ripplecraftfacades.com</p>
</section>

<section class="card card--back" aria-label="Business card back">
  <div class="brand"><span class="brand__square"></span>Ripplecraft Facades</div>
  <p class="tagline">decorative panels for<br>interiors &amp; landscapes</p>
</section>

</body>
</html>
```